RWT Fittings Ltd Business Cards

We need a business card with our business logo. We provide window and door installations on high-rises in west coast British Colombia, Canada.

I would like my business information and details on one side of the card, and the other side the company name with logo

Target Market(s)

General Contractors

Industry/Entity Type

Construction

Contact Information for Business Card

one side i want my company name and logo in the dark theme logo that i provided

Requirements
Must have
• Marco Peltieri, 16045518293, RWTFittings@mailbox-demo.com, 1407-5194 Linden Row Burnaby BC, V5H 2K9, Owner & Manager

```html
<!DOCTYPE html>
<html lang="en">
<head>
<meta charset="utf-8">
<title>RWT Fittings Ltd – Business Cards</title>
<link rel="stylesheet" href="https://fonts.googleapis.com/css2?family=Lato:wght@400;700&family=Montserrat:wght@400;700&display=swap">
<style>
  :root {
    --backdrop: #1f2124;
    --card: #3a3a3c;
    --card-edge: #2c2c2e;
    --accent: #29a8e0;
    --text-light: #e9e9ea;
    --text-muted: #c9c9cb;
  }
  * { margin: 0; padding: 0; box-sizing: border-box; }
  html, body {
    width: 1200px;
    height: 952px;
    overflow: hidden;
    background: var(--backdrop);
  }
  .stage {
    width: 1200px;
    height: 952px;
    display: flex;
    align-items: center;
    justify-content: center;
    gap: 60px;
  }
  .card {
    position: relative;
    width: 530px;
    height: 303px;
    border-radius: 24px;
    background: var(--card);
    box-shadow: 0 4px 0 var(--card-edge), 0 8px 0 var(--card-edge), 0 18px 30px rgba(0,0,0,0.45);
    overflow: hidden;
  }

  /* Brand mark: name set in text with one plain square */
  .brand {
    display: flex;
    align-items: center;
    gap: 12px;
    color: var(--accent);
    font-family: "Montserrat", sans-serif;
    font-weight: 700;
    white-space: nowrap;
  }
  .brand__square {
    background: var(--accent);
    flex: none;
  }

  /* Contact side */
  .card--contact .brand {
    position: absolute;
    left: 44px;
    top: 36px;
    font-size: 26px;
  }
  .card--contact .brand__square { width: 22px; height: 22px; }

  .contact-list {
    position: absolute;
    left: 44px;
    top: 106px;
    list-style: none;
    font-family: "Lato", sans-serif;
    font-size: 13px;
    line-height: 1.35;
    color: var(--text-light);
  }
  .contact-list li {
    display: flex;
    align-items: flex-start;
    gap: 10px;
    margin-bottom: 8px;
  }
  .contact-icon {
    flex: none;
    width: 16px;
    height: 16px;
    margin-top: 1px;
  }

  .person {
    position: absolute;
    right: 40px;
    bottom: 30px;
    text-align: right;
  }
  .person__name {
    font-family: "Montserrat", sans-serif;
    font-size: 25px;
    letter-spacing: 0.5px;
    color: var(--accent);
    text-transform: uppercase;
    white-space: nowrap;
  }
  .person__name .first { font-weight: 400; }
  .person__name .last { font-weight: 700; }
  .person__role {
    margin-top: 2px;
    font-family: "Lato", sans-serif;
    font-size: 15px;
    color: var(--text-light);
  }

  /* Brand side */
  .card--brand {
    display: flex;
    align-items: center;
    justify-content: center;
  }
  .card--brand .brand { font-size: 36px; gap: 16px; }
  .card--brand .brand__square { width: 30px; height: 30px; }
</style>
</head>
<body>
<main class="stage">

  <section class="card card--contact" aria-label="Business card, contact side">
    <div class="brand"><span class="brand__square"></span>RWT Fittings Ltd</div>

    <ul class="contact-list">
      <li>
        <svg class="contact-icon" viewBox="0 0 16 16" aria-hidden="true">
          <rect width="16" height="16" rx="3" fill="#29a8e0"/>
          <path d="M8 3.2a3 3 0 0 0-3 3c0 2.2 3 6 3 6s3-3.8 3-6a3 3 0 0 0-3-3z" fill="#fff"/>
          <circle cx="8" cy="6.2" r="1.1" fill="#29a8e0"/>
        </svg>
        <span>1407-5194 Linden Row<br>Burnaby BC, V5H 2K9</span>
      </li>
      <li>
        <svg class="contact-icon" viewBox="0 0 16 16" aria-hidden="true">
          <rect width="16" height="16" rx="3" fill="#29a8e0"/>
          <path d="M5.2 3.5l1.6 2.2-1 1.1a6 6 0 0 0 3.4 3.4l1.1-1 2.2 1.6-.8 1.6c-4 0-8.3-4.3-8.3-8.3z" fill="#fff"/>
        </svg>
        <span>16045518293</span>
      </li>
      <li>
        <svg class="contact-icon" viewBox="0 0 16 16" aria-hidden="true">
          <rect width="16" height="16" rx="3" fill="#29a8e0"/>
          <rect x="3.5" y="5" width="9" height="6.5" rx="0.8" fill="#fff"/>
          <path d="M3.8 5.4L8 8.6l4.2-3.2" stroke="#29a8e0" stroke-width="1" fill="none"/>
        </svg>
        <span>RWTFittings@mailbox-demo.com</span>
      </li>
      <li>
        <svg class="contact-icon" viewBox="0 0 16 16" aria-hidden="true">
          <rect width="16" height="16" rx="3" fill="#29a8e0"/>
          <path d="M5 3.5l6.5 4.6-2.8.5 1.6 3-1.2.6-1.6-3-2 1.9z" fill="#fff"/>
        </svg>
        <span>www.rwtfittings-demo.com</span>
      </li>
    </ul>

    <div class="person">
      <p class="person__name"><span class="first">Marco</span> <span class="last">Peltieri</span></p>
      <p class="person__role">Owner &amp; Manager</p>
    </div>
  </section>

  <section class="card card--brand" aria-label="Business card, brand side">
    <div class="brand"><span class="brand__square"></span>RWT Fittings Ltd</div>
  </section>

</main>
</body>
</html>
```